Thibodeaux Creole

I am launching a new Cajun Steakhouse.
We have purchased a food truck to support the restaurant and sell some our food until the opening in March. 2025. The truck has a white blank canvas on all sides. The right side has multiple raised surfaces (Serving widow,, TV enclosure with speakers, pop up fold-down service table. There is a sliding door on the right with two windows. The bottom window will be covered in wrap. The primary color will be black. Need a bold and fresh design. A Look that will stand out but not be over the top. The truck is a 18’ Ironmule truck (QMB Trick). I have included pictures of the truck, our logo, some pictures of some of the meals that will be served from the truck, a picture of our already branded catering truck, and various other promotional branding we use. The Food truck doesn’t have to look exactly like our catering truck, but I want to keep the black background with our colorful logo. Everything else is can be created.
Our specialty is Garlic Dungenes Crab and that needs to be highlighted (The Best in the Bay).

Target Market(s)

General Public

Industry/Entity Type

Food Service

Font styles to use
Serif
Sans Serif
Decorative
Script

Requirements
Must have
• Black base wrap color
Nice to have
• Look at the mock up on the trash can photo with the little crabs. I think it would look cool on the wrap.
Should not have
• Our specialty is garlic Crabs. So we need to Highlight somewhere (The best crab in the bay)

```html
<!DOCTYPE html>
<html lang="en">
<head>
<meta charset="utf-8">
<title>Thibodeaux Creole Steakhouse – Food Truck Wrap</title>
<link rel="stylesheet" href="https://fonts.googleapis.com/css2?family=Cinzel:wght@400;600&family=Poppins:wght@600&display=swap">
<style>
  :root {
    --page: #ffffff;
    --wrap-black: #1b1b1b;
    --ink-white: #ffffff;
    --brand-orange: #f39a1f;
    --grad-green: #9bc53d;
    --grad-orange: #f7941d;
    --grad-pink: #e8245c;
    --crab-red: #e8602a;
    --crab-light: #f28a4a;
    --divider: #5a1a22;
  }
  * { box-sizing: border-box; margin: 0; padding: 0; }
  html, body {
    width: 1200px; height: 1192px; overflow: hidden;
    background: var(--page);
  }
  .wrap-panel {
    position: absolute;
    left: 50px; top: 404px;
    width: 1100px; height: 384px;
    background: var(--wrap-black);
  }
  .brand-mark {
    position: absolute;
    left: 452px; top: 40px;
    width: 70px; height: 70px;
    border-radius: 50%;
    background: var(--brand-orange);
  }
  .brand-name {
    position: absolute;
    left: 300px; top: 150px;
    width: 374px;
    text-align: center;
    font-family: 'Cinzel', serif;
    font-weight: 400;
    color: var(--brand-orange);
    line-height: 1.1;
  }
  .brand-name .line-main { display: block; font-size: 33px; }
  .brand-name .line-sub { display: block; font-size: 24px; letter-spacing: 4px; }
  .divider {
    position: absolute;
    left: 663px; top: 150px;
    width: 1px; height: 80px;
    background: var(--divider);
  }
  .tagline {
    position: absolute;
    left: 684px; top: 144px;
    font-family: 'Cinzel', serif;
    font-weight: 400;
    font-size: 41px;
    line-height: 1.0;
    color: var(--ink-white);
  }
  .tagline .highlight {
    background: linear-gradient(90deg, var(--grad-orange), var(--grad-green));
    -webkit-background-clip: text; background-clip: text;
    color: transparent;
  }
  .crab-art {
    position: absolute;
    left: 205px; top: 256px;
    width: 118px; height: 110px;
    border-radius: 50%;
    background: radial-gradient(circle at 50% 50%, var(--crab-light), var(--crab-red) 70%, transparent 72%);
  }
  .website {
    position: absolute;
    left: 335px; top: 262px;
    width: 300px;
    text-align: center;
    font-family: 'Cinzel', serif;
    font-size: 17px;
    letter-spacing: 4px;
    color: var(--ink-white);
  }
  .phone {
    position: absolute;
    left: 335px; top: 286px;
    font-family: 'Poppins', sans-serif;
    font-weight: 600;
    font-size: 39px;
    letter-spacing: 0.5px;
    background: linear-gradient(90deg, var(--grad-pink), var(--grad-orange) 45%, var(--grad-green));
    -webkit-background-clip: text; background-clip: text;
    color: transparent;
  }
</style>
</head>
<body>
  <section class="wrap-panel" aria-label="Food truck side wrap">
    <div class="brand-mark"></div>
    <h1 class="brand-name">
      <span class="line-main">THIBODEAUX CREOLE</span>
      <span class="line-sub">STEAKHOUSE</span>
    </h1>
    <div class="divider"></div>
    <p class="tagline">THE BEST <span class="highlight">CRAB</span><br>IN THE BAY</p>
    <div class="crab-art" role="img" aria-label="Illustration of a cooked red Dungeness crab"></div>
    <p class="website">THIBCREOLE.COM</p>
    <p class="phone">(555) 014-2287</p>
  </section>
</body>
</html>
```